Geschäftspapiere für Handwerksunternehmen
Zielgruppe
Handwerk
Elektroinstallation
Design Modern
Aufgabenstellung
Anschrift, Kontaktdaten, Bankverbindung, Logo,
Im Haselgrund 9 77463 Lindenweiler Inhaber Lenno Brüchert
Telefon: 07412-6640285 Email: info@rvb-stromtechnik.de Internet: www.rvb-stromtechnik.de
Finanzamt Dornhalden USt.-ID: DE574016328 Steuer Nr.:4190357762
Kreisbank Talgau IBAN:DE71480392610007315946 BIC:KRTAGES1XYZ

```html
<!DOCTYPE html>
<html lang="de">
<head>
<meta charset="utf-8">
<title>RVB Stromtechnik – Briefbogen</title>
<link href="https://fonts.googleapis.com/css2?family=Arimo:wght@400;700&display=swap" rel="stylesheet">
<style>
  :root {
    --ink: #111111;
    --brand-yellow: #f4ee3c;
    --brand-yellow-faint: rgba(244, 238, 60, 0.16);
    --paper: #ffffff;
  }
  * { margin: 0; padding: 0; box-sizing: border-box; }
  html, body { width: 848px; height: 1200px; overflow: hidden; background: var(--paper); }
  body { font-family: "Arimo", Arial, sans-serif; color: var(--ink); }
  .sheet { position: relative; width: 848px; height: 1200px; overflow: hidden; }

  .backdrop-circle {
    position: absolute; left: 590px; top: 640px; width: 330px; height: 330px;
    border-radius: 50%; background: var(--brand-yellow-faint);
  }

  .brand { position: absolute; top: 40px; left: 0; width: 848px;
    display: flex; justify-content: center; align-items: center; gap: 16px; }
  .brand-dot { width: 58px; height: 58px; border-radius: 50%; background: var(--brand-yellow); }
  .brand-name { font-size: 44px; font-weight: 700; color: var(--ink); letter-spacing: 1px; }

  .return-line { position: absolute; top: 164px; left: 106px; font-size: 9.5px; white-space: nowrap; }

  .recipient { position: absolute; top: 230px; left: 106px; font-size: 15.5px; line-height: 17.4px; font-style: normal; }
  .recipient .company { font-weight: 700; }

  .contact-info { position: absolute; top: 265px; left: 509px; font-size: 15.5px; line-height: 17.2px; white-space: nowrap; }
  .contact-info .label { font-size: 10.5px; }
  .contact-info .date { margin-top: 17px; }

  .subject { position: absolute; top: 405px; left: 101px; font-size: 15px; font-weight: 700; }

  .letter-body { position: absolute; top: 459px; left: 101px; width: 720px; font-size: 15.5px; line-height: 18px; }
  .letter-body p { margin-bottom: 18px; }
  .letter-body .sender-company { margin-top: 36px; }

  .footer { position: absolute; top: 1097px; left: 101px; font-size: 9.5px; line-height: 11.4px; }
  .footer .col { position: absolute; top: 0; white-space: nowrap; }
  .footer .col-company { left: 0; }
  .footer .col-owner { left: 126px; }
  .footer .col-contact { left: 268px; }
  .footer .col-bank { left: 465px; }
  .footer .gap { height: 11.4px; }
  .footer dl { display: grid; grid-template-columns: 49px auto; }
  .footer .bank-grid { grid-template-columns: 34px auto; }
</style>
</head>
<body>
<div class="sheet">
  <div class="backdrop-circle" aria-hidden="true"></div>

  <header class="brand">
    <span class="brand-dot" aria-hidden="true"></span>
    <span class="brand-name">RVB Stromtechnik</span>
  </header>

  <div class="return-line">Lenno Brüchert ◆ Im Haselgrund 9 ◆ 77463 Lindenweiler</div>

  <address class="recipient">
    <div class="company">Musterfirma</div>
    <div>Max Mustermann</div>
    <div>Musterstraße 1</div>
    <div>00000 Musterort</div>
    <div>Deutschland</div>
  </address>

  <div class="contact-info">
    <div><span class="label">Name:</span> Lenno Brüchert</div>
    <div><span class="label">Telefon:</span> 07412 6640285</div>
    <div><span class="label">Telefax:</span> in Bearbeitung</div>
    <div><span class="label">E-Mail:</span> info@rvb-stromtechnik.de</div>
    <div class="date"><span class="label">Datum:</span> 00.00.2020</div>
  </div>

  <div class="subject">Betreff/ Auftragsnummer etc.</div>

  <main class="letter-body">
    <p>Sehr geehrter Herr Mustermann,</p>
    <p>wie gerade telefonisch besprochen möchten wir den oben aufgeführten Auftrag 1 Jahr testen und möchten vorerst auf eine automatische Verlängerung um 1 Jahr verzichten.</p>
    <p>Wir kündigen daher den mit Ihnen bestehenden Vertrag, fristgerecht, zum 31.08.2021, hilfsweise zum nächstmöglichen Termin.</p>
    <p>Wir freuen uns dennoch auf eine gute Zusammenarbeit mit Ihnen.</p>
    <p>Mit freundlichen Grüßen</p>
    <p class="sender-company">RVB Stromtechnik</p>
    <p>(Unterschrift)</p>
    <p>Lenno Brüchert</p>
  </main>

  <footer class="footer">
    <div class="col col-company">
      <div>RVB Stromtechnik</div>
      <div class="gap"></div>
      <div>Herr</div>
      <div>Lenno Brüchert</div>
      <div>Im Haselgrund 9</div>
      <div>77463 Lindenweiler</div>
    </div>
    <div class="col col-owner">
      <div>Inhaber:</div>
      <div>Lenno Brüchert</div>
      <div class="gap"></div>
      <div>Finanzamt Dornhalden</div>
      <div>EG-Identnr.: DE574016328</div>
      <div>Steuernr.:&nbsp;&nbsp;&nbsp;&nbsp;&nbsp;4190357762</div>
    </div>
    <div class="col col-contact">
      <dl>
        <dt>Telefon:</dt><dd>07412 6640285</dd>
        <dt>Fax:</dt><dd>In Bearbeitung</dd>
        <dt>Internet:</dt><dd>www.rvb-stromtechnik.de</dd>
        <dt>E-Mail:</dt><dd>info@rvb-stromtechnik.de</dd>
      </dl>
    </div>
    <div class="col col-bank">
      <div>Kreisbank Talgau</div>
      <div class="gap"></div>
      <dl class="bank-grid">
        <dt>IBAN</dt><dd>DE71480392610007315946</dd>
        <dt>BIC</dt><dd>KRTAGES1XYZ</dd>
      </dl>
    </div>
  </footer>
</div>
</body>
</html>
```